Logo & nopcommerce theme design for a webshop in gadgets & lifestyle products

We are looking for someone who can design a logo and a nopcommerce theme for our webshop. The name of the shop is Lumavorp. The logo should also be used for plaztrove. In the attached file we have an example of a theme that is close what we are looking for. The coloring should be different but the lay-out is ok. Only on the left we want a column to choose a sub category and a column where you can set some filters to search in detail for a product.

Industry/Entity Type

Shop

Number of Pages Required

1 page

Requirements
Must have
• The Nopcommerce theme for 3.40 should have a professional look, not to color full and for the rest we leave it to the designer
Nice to have
• n/a
Should not have
• n/a

```html
<!DOCTYPE html>
<html lang="en">
<head>
<meta charset="utf-8">
<title>Lumavorp – Online Store</title>
<link href="https://fonts.googleapis.com/css2?family=Open+Sans:ital,wght@0,400;0,600;0,700;1,400&display=swap" rel="stylesheet">
<style>
:root{
  --page:#303030;
  --panel:#000000;
  --bar:#1c1c1c;
  --accent:#9f9a35;
  --text:#ffffff;
  --muted:#bdbdbd;
  --line:#2e2e2e;
  --photo:#e4e5e7;
  --footer:#8f8b31;
  --footer-line:#b5b263;
}
*{box-sizing:border-box;margin:0;padding:0}
html,body{width:1200px;height:2571px;overflow:hidden}
body{background:var(--page);font-family:"Open Sans",Arial,sans-serif;color:var(--text);position:relative}
ul{list-style:none}

/* top bar */
.topbar{position:absolute;left:0;top:0;width:1200px;height:38px;background:var(--bar);border-top:4px solid var(--accent)}
.topbar-links{position:absolute;left:181px;top:10px;font-size:11px;display:flex;align-items:center;gap:6px}
.topbar-links b{font-weight:700}
.lang-currency{position:absolute;left:878px;top:0;height:34px;display:flex;font-size:11px}
.lang-currency span{display:block;padding:0 7px;line-height:34px}
.lang-currency .active{background:var(--accent)}
.lang-currency .sep{width:8px;padding:0}

/* header */
.logo{position:absolute;left:183px;top:69px;display:flex;align-items:center;gap:12px}
.logo-mark{width:38px;height:38px;background:var(--accent)}
.logo-name{font-size:42px;font-weight:400;letter-spacing:-.5px;line-height:1}
.logo-tag{position:absolute;left:173px;top:46px;font-size:8px;letter-spacing:1.5px;color:var(--muted);white-space:nowrap}
.search{position:absolute;left:787px;top:80px;width:231px;height:33px;background:#fff;display:flex;align-items:center;padding:0 8px;color:#666;font-size:10px}
.search svg{position:absolute;right:8px;top:8px}

/* nav */
.mainnav{position:absolute;left:183px;top:154px;width:837px;height:35px;background:var(--panel);display:flex}
.mainnav a{font-size:12px;padding:0 12px;line-height:35px}
.mainnav a.current{background:var(--accent);padding:0 17px}

/* sidebar */
.side-box{position:absolute;left:183px;width:172px;background:var(--panel)}
.categories{top:235px;height:423px}
.side-title{font-size:16px;font-weight:400;padding:0 12px;line-height:28px;border-bottom:1px solid var(--line)}
.categories .side-title{margin-top:6px}
.cat-list li{font-size:10px;line-height:30px;padding:0 13px}
.cat-list li.current{background:var(--accent)}
.filters{top:682px;height:1034px;padding-top:6px}
.filter-group{margin-bottom:13px}
.filter-group .side-title{margin-bottom:2px}
.filter-group li{font-size:10px;line-height:30px;padding-left:13px;display:flex;align-items:center;gap:12px}
.filter-group li i{width:10px;height:10px;background:#fff;display:block}

/* toolbar */
.toolbar{position:absolute;left:369px;top:231px;width:649px;height:35px;background:var(--panel);font-size:10px;display:flex;align-items:center;padding:0 14px}
.toolbar .low{color:var(--accent);text-decoration:underline;margin:0 8px}
.toolbar .right{margin-left:auto;display:flex;align-items:center;gap:10px}
.toolbar .olive{color:var(--accent)}
.select{width:84px;height:20px;background:#3a3a3a;display:flex;align-items:center;justify-content:space-between;padding:0 6px}

/* products */
.products{position:absolute;left:369px;top:295px;display:grid;grid-template-columns:repeat(3,197px);grid-auto-rows:237px;gap:29px}
.card{background:var(--panel);padding:7px 7px 0;position:relative}
.photo{height:146px;background:var(--photo)}
.p-dark{background:radial-gradient(ellipse 38% 34% at 50% 52%,#1e1f21 0%,#3b3c3f 55%,var(--photo) 100%)}
.p-white{background:radial-gradient(ellipse 40% 38% at 50% 52%,#f7f7f7 0%,#b9bbbe 60%,var(--photo) 100%)}
.p-glasses{background:linear-gradient(180deg,var(--photo) 30%,#1c1c1c 44%,#2a2a2a 52%,var(--photo) 66%)}
.p-silver{background:radial-gradient(ellipse 42% 36% at 50% 54%,#8d8f92 0%,#b3b5b8 55%,var(--photo) 100%)}
.p-mouse{background:radial-gradient(ellipse 22% 36% at 50% 50%,#121314 0%,#2a3550 50%,var(--photo) 100%)}
.p-bottle{background:radial-gradient(ellipse 14% 44% at 50% 50%,#f2f4f6 0%,#4f9bc4 45%,var(--photo) 100%)}
.p-speaker{background:radial-gradient(ellipse 34% 38% at 50% 50%,#1a1a1a 0%,#f2f3f4 55%,var(--photo) 100%)}
.p-tablet{background:linear-gradient(160deg,var(--photo) 28%,#0d0d12 42%,#2b1e4a 55%,#0d0d12 66%,var(--photo) 76%)}
.p-phones{background:radial-gradient(ellipse 40% 44% at 50% 50%,#2a2b2e 0%,#d3d5d8 60%,var(--photo) 100%)}
.p-waffle{background:radial-gradient(ellipse 42% 34% at 50% 58%,#d7a248 0%,#1c1c1c 55%,var(--photo) 100%)}
.p-wood{background:radial-gradient(circle at 48% 50%,#c8582f 0%,#3a3a3a 18%,#9a9ea2 26%,#a8643a 34%,#7d4624 100%)}
.p-tv{background:radial-gradient(ellipse 40% 34% at 48% 48%,#f5c31c 0%,#e0461c 50%,#1a1a1a 75%,var(--photo) 100%)}
.p-wooden{background:radial-gradient(ellipse 34% 42% at 50% 52%,#b07a45 0%,#2a2420 55%,var(--photo) 100%)}
.p-phoneblue{background:radial-gradient(ellipse 26% 44% at 50% 50%,#4d86c6 0%,#f2f3f5 55%,var(--photo) 100%)}
.card-name{font-size:9px;margin-top:10px;padding-left:6px;color:#ddd}
.card-price{font-size:16px;padding-left:6px;line-height:18px}
.card-foot{position:absolute;left:0;right:0;bottom:0;height:36px;border-top:1px solid var(--line);display:flex;align-items:center;font-size:9px;padding-left:13px}
.card-foot s{margin-left:3px}
.cart-btn{position:absolute;right:0;top:0;width:36px;height:35px;border-left:1px solid var(--line);display:flex;align-items:center;justify-content:center}

/* pagination */
.pager{position:absolute;left:369px;top:2150px;width:649px;height:34px;background:var(--panel);display:flex;align-items:center;justify-content:center;font-size:10px;gap:10px}
.pager .arrow{color:var(--accent);font-size:14px;margin:0 22px}
.pager .on{text-decoration:underline;font-weight:700}
.pager .bar{color:#666}
.showing{position:absolute;left:369px;top:2196px;width:649px;text-align:center;font-size:9px;font-style:italic;color:#ddd}

/* footer */
.footer{position:absolute;left:0;top:2263px;width:1200px;height:236px;background:var(--footer)}
.footer-col{position:absolute;top:32px;width:188px}
.footer-col h4{font-size:15px;font-weight:400;padding-bottom:8px;border-bottom:1px solid var(--footer-line);margin-bottom:12px}
.footer-col li{font-size:9.5px;line-height:28px;display:flex;align-items:center;gap:10px}
.bottombar{position:absolute;left:0;top:2499px;width:1200px;height:72px;background:var(--page);font-size:9.5px}
.copyright{position:absolute;left:183px;top:29px}
.social{position:absolute;left:0;width:1200px;top:24px;display:flex;justify-content:center;gap:14px;font-size:12px;font-weight:600}
</style>
</head>
<body>

<header class="topbar">
  <div class="topbar-links">
    <svg width="13" height="12" viewBox="0 0 24 24"><path fill="#fff" d="M6.6 10.8a15 15 0 0 0 6.6 6.6l2.2-2.2c.3-.3.7-.4 1-.2 1.1.4 2.3.6 3.6.6.6 0 1 .4 1 1V20c0 .6-.4 1-1 1A17 17 0 0 1 3 4c0-.6.4-1 1-1h3.5c.6 0 1 .4 1 1 0 1.3.2 2.5.6 3.6.1.3 0 .7-.2 1z"/></svg>
    <span><b>Call us:</b> (0000) 000 0000</span><span>•</span><span>Signup</span><span>•</span><span>Sign in</span><span>•</span><span>Cart</span>
  </div>
  <div class="lang-currency">
    <span class="active">EN</span><span>FR</span><span>GM</span><span class="sep"></span>
    <span class="active">$</span><span>€</span><span>£</span>
  </div>
</header>

<div class="logo">
  <div class="logo-mark"></div>
  <div class="logo-name">Lumavorp</div>
  <div class="logo-tag">ONLINE STORE</div>
</div>

<div class="search">Search entire store here.......
  <svg width="16" height="16" viewBox="0 0 24 24"><circle cx="10" cy="10" r="6.5" fill="none" stroke="#9f9a35" stroke-width="3"/><path d="M15 15l6 6" stroke="#9f9a35" stroke-width="3.5" stroke-linecap="round"/></svg>
</div>

<nav class="mainnav">
  <a class="current">Home</a><a>About us</a><a>Products</a><a>Register</a><a>Shop</a><a>Contact Us</a>
</nav>

<aside class="side-box categories">
  <h3 class="side-title">Categories</h3>
  <ul class="cat-list">
    <li>Sofas</li><li class="current">Gadgets</li><li>Lifestyle</li><li>Chairs</li><li>Tables</li><li>Beds</li><li>Storage</li><li>Lighting</li><li>Art</li><li>Homeware</li><li>Home Textiles</li><li>Designer</li><li>UNBOXED</li>
  </ul>
</aside>

<aside class="side-box filters">
  <div class="filter-group"><h3 class="side-title">Thread Count</h3>
    <ul><li><i></i>200</li><li><i></i>300</li></ul></div>
  <div class="filter-group"><h3 class="side-title">Bedding Size</h3>
    <ul><li><i></i>Single</li><li><i></i>Double</li><li><i></i>Kingsize</li><li><i></i>Super King</li><li><i></i>Pillow Case</li></ul></div>
  <div class="filter-group"><h3 class="side-title">Availability</h3>
    <ul><li><i></i>1 Week</li><li><i></i>1 Week</li><li><i></i>6 Week</li><li><i></i>10 Week</li></ul></div>
  <div class="filter-group"><h3 class="side-title">Colour</h3>
    <ul><li><i></i>Blues</li><li><i></i>Browns</li><li><i></i>Colourful</li><li><i></i>Greys</li><li><i></i>Metallic</li><li><i></i>Neeutrals</li><li><i></i>Oak</li><li><i></i>Patterned</li><li><i></i>Purples</li><li><i></i>Turquoise</li><li><i></i>Whites</li></ul></div>
  <div class="filter-group"><h3 class="side-title">Price</h3>
    <ul><li><i></i>$0 - $ 250</li><li><i></i>$250 - $ 500</li><li><i></i>$500 - $ 750</li><li><i></i>$750 - $ 1000</li><li><i></i>$1000 - $ 1250</li></ul></div>
</aside>

<div class="toolbar">
  <span>Sort by price:</span><span class="low">Low</span><span>|</span><span style="margin-left:8px">High</span>
  <div class="right">
    <span class="olive">Sort By</span><span class="select">Position <span>⇕</span></span>
    <span class="olive" style="margin-left:12px">Show</span><span class="select">Position <span>⇕</span></span>
    <span style="margin-left:6px">Per Page</span>
  </div>
</div>

<main class="products">
  <article class="card"><div class="photo p-dark" role="img" aria-label="Black digital SLR camera"></div><p class="card-name">Fontry Double Bed, Oak</p><p class="card-price">$749</p><div class="card-foot">Typical high street <s>$1,095*</s><span class="cart-btn"><svg width="16" height="15" viewBox="0 0 24 22"><path d="M1 2h4l3 12h12l3-9H7" fill="none" stroke="#9f9a35" stroke-width="2.4"/><circle cx="10" cy="19" r="2" fill="#9f9a35"/><circle cx="18" cy="19" r="2" fill="#9f9a35"/></svg></span></div></article>
  <article class="card"><div class="photo p-white" role="img" aria-label="White over-ear headphones"></div><p class="card-name">Fontry Double Bed, Oak</p><p class="card-price">$749</p><div class="card-foot">Typical high street <s>$1,095*</s><span class="cart-btn"><svg width="16" height="15" viewBox="0 0 24 22"><path d="M1 2h4l3 12h12l3-9H7" fill="none" stroke="#9f9a35" stroke-width="2.4"/><circle cx="10" cy="19" r="2" fill="#9f9a35"/><circle cx="18" cy="19" r="2" fill="#9f9a35"/></svg></span></div></article>
  <article class="card"><div class="photo p-glasses" role="img" aria-label="Black sunglasses"></div><p class="card-name">Fontry Double Bed, Oak</p><p class="card-price">$749</p><div class="card-foot">Typical high street <s>$1,095*</s><span class="cart-btn"><svg width="16" height="15" viewBox="0 0 24 22"><path d="M1 2h4l3 12h12l3-9H7" fill="none" stroke="#9f9a35" stroke-width="2.4"/><circle cx="10" cy="19" r="2" fill="#9f9a35"/><circle cx="18" cy="19" r="2" fill="#9f9a35"/></svg></span></div></article>
  <article class="card"><div class="photo p-silver" role="img" aria-label="Silver DJ turntable"></div><p class="card-name">Fontry Double Bed, Oak</p><p class="card-price">$749</p><div class="card-foot">Typical high street <s>$1,095*</s><span class="cart-btn"><svg width="16" height="15" viewBox="0 0 24 22"><path d="M1 2h4l3 12h12l3-9H7" fill="none" stroke="#9f9a35" stroke-width="2.4"/><circle cx="10" cy="19" r="2" fill="#9f9a35"/><circle cx="18" cy="19" r="2" fill="#9f9a35"/></svg></span></div></article>
  <article class="card"><div class="photo p-mouse" role="img" aria-label="Black wireless mouse"></div><p class="card-name">Fontry Double Bed, Oak</p><p class="card-price">$749</p><div class="card-foot">Typical high street <s>$1,095*</s><span class="cart-btn"><svg width="16" height="15" viewBox="0 0 24 22"><path d="M1 2h4l3 12h12l3-9H7" fill="none" stroke="#9f9a35" stroke-width="2.4"/><circle cx="10" cy="19" r="2" fill="#9f9a35"/><circle cx="18" cy="19" r="2" fill="#9f9a35"/></svg></span></div></article>
  <article class="card"><div class="photo p-bottle" role="img" aria-label="Filter water bottle"></div><p class="card-name">Fontry Double Bed, Oak</p><p class="card-price">$749</p><div class="card-foot">Typical high street <s>$1,095*</s><span class="cart-btn"><svg width="16" height="15" viewBox="0 0 24 22"><path d="M1 2h4l3 12h12l3-9H7" fill="none" stroke="#9f9a35" stroke-width="2.4"/><circle cx="10" cy="19" r="2" fill="#9f9a35"/><circle cx="18" cy="19" r="2" fill="#9f9a35"/></svg></span></div></article>
  <article class="card"><div class="photo p-speaker" role="img" aria-label="Round white speaker"></div><p class="card-name">Fontry Double Bed, Oak</p><p class="card-price">$749</p><div class="card-foot">Typical high street <s>$1,095*</s><span class="cart-btn"><svg width="16" height="15" viewBox="0 0 24 22"><path d="M1 2h4l3 12h12l3-9H7" fill="none" stroke="#9f9a35" stroke-width="2.4"/><circle cx="10" cy="19" r="2" fill="#9f9a35"/><circle cx="18" cy="19" r="2" fill="#9f9a35"/></svg></span></div></article>
  <article class="card"><div class="photo p-tablet" role="img" aria-label="Black tablet computer"></div><p class="card-name">Fontry Double Bed, Oak</p><p class="card-price">$749</p><div class="card-foot">Typical high street <s>$1,095*</s><span class="cart-btn"><svg width="16" height="15" viewBox="0 0 24 22"><path d="M1 2h4l3 12h12l3-9H7" fill="none" stroke="#9f9a35" stroke-width="2.4"/><circle cx="10" cy="19" r="2" fill="#9f9a35"/><circle cx="18" cy="19" r="2" fill="#9f9a35"/></svg></span></div></article>
  <article class="card"><div class="photo p-phones" role="img" aria-label="Two smartphones in white and black"></div><p class="card-name">Fontry Double Bed, Oak</p><p class="card-price">$749</p><div class="card-foot">Typical high street <s>$1,095*</s><span class="cart-btn"><svg width="16" height="15" viewBox="0 0 24 22"><path d="M1 2h4l3 12h12l3-9H7" fill="none" stroke="#9f9a35" stroke-width="2.4"/><circle cx="10" cy="19" r="2" fill="#9f9a35"/><circle cx="18" cy="19" r="2" fill="#9f9a35"/></svg></span></div></article>
  <article class="card"><div class="photo p-dark" role="img" aria-label="Lens-style camera attachment"></div><p class="card-name">Fontry Double Bed, Oak</p><p class="card-price">$749</p><div class="card-foot">Typical high street <s>$1,095*</s><span class="cart-btn"><svg width="16" height="15" viewBox="0 0 24 22"><path d="M1 2h4l3 12h12l3-9H7" fill="none" stroke="#9f9a35" stroke-width="2.4"/><circle cx="10" cy="19" r="2" fill="#9f9a35"/><circle cx="18" cy="19" r="2" fill="#9f9a35"/></svg></span></div></article>
  <article class="card"><div class="photo p-waffle" role="img" aria-label="Waffle maker with a golden waffle"></div><p class="card-name">Fontry Double Bed, Oak</p><p class="card-price">$749</p><div class="card-foot">Typical high street <s>$1,095*</s><span class="cart-btn"><svg width="16" height="15" viewBox="0 0 24 22"><path d="M1 2h4l3 12h12l3-9H7" fill="none" stroke="#9f9a35" stroke-width="2.4"/><circle cx="10" cy="19" r="2" fill="#9f9a35"/><circle cx="18" cy="19" r="2" fill="#9f9a35"/></svg></span></div></article>
  <article class="card"><div class="photo p-dark" role="img" aria-label="Black digital sports watch"></div><p class="card-name">Fontry Double Bed, Oak</p><p class="card-price">$749</p><div class="card-foot">Typical high street <s>$1,095*</s><span class="cart-btn"><svg width="16" height="15" viewBox="0 0 24 22"><path d="M1 2h4l3 12h12l3-9H7" fill="none" stroke="#9f9a35" stroke-width="2.4"/><circle cx="10" cy="19" r="2" fill="#9f9a35"/><circle cx="18" cy="19" r="2" fill="#9f9a35"/></svg></span></div></article>
  <article class="card"><div class="photo p-silver" role="img" aria-label="Silver smartwatch"></div><p class="card-name">Fontry Double Bed, Oak</p><p class="card-price">$749</p><div class="card-foot">Typical high street <s>$1,095*</s><span class="cart-btn"><svg width="16" height="15" viewBox="0 0 24 22"><path d="M1 2h4l3 12h12l3-9H7" fill="none" stroke="#9f9a35" stroke-width="2.4"/><circle cx="10" cy="19" r="2" fill="#9f9a35"/><circle cx="18" cy="19" r="2" fill="#9f9a35"/></svg></span></div></article>
  <article class="card"><div class="photo p-wood" role="img" aria-label="Round smart thermostat on a wooden wall"></div><p class="card-name">Fontry Double Bed, Oak</p><p class="card-price">$749</p><div class="card-foot">Typical high street <s>$1,095*</s><span class="cart-btn"><svg width="16" height="15" viewBox="0 0 24 22"><path d="M1 2h4l3 12h12l3-9H7" fill="none" stroke="#9f9a35" stroke-width="2.4"/><circle cx="10" cy="19" r="2" fill="#9f9a35"/><circle cx="18" cy="19" r="2" fill="#9f9a35"/></svg></span></div></article>
  <article class="card"><div class="photo p-dark" role="img" aria-label="Solid state drives"></div><p class="card-name">Fontry Double Bed, Oak</p><p class="card-price">$749</p><div class="card-foot">Typical high street <s>$1,095*</s><span class="cart-btn"><svg width="16" height="15" viewBox="0 0 24 22"><path d="M1 2h4l3 12h12l3-9H7" fill="none" stroke="#9f9a35" stroke-width="2.4"/><circle cx="10" cy="19" r="2" fill="#9f9a35"/><circle cx="18" cy="19" r="2" fill="#9f9a35"/></svg></span></div></article>
  <article class="card"><div class="photo p-phoneblue" role="img" aria-label="White smartphone"></div><p class="card-name">Fontry Double Bed, Oak</p><p class="card-price">$749</p><div class="card-foot">Typical high street <s>$1,095*</s><span class="cart-btn"><svg width="16" height="15" viewBox="0 0 24 22"><path d="M1 2h4l3 12h12l3-9H7" fill="none" stroke="#9f9a35" stroke-width="2.4"/><circle cx="10" cy="19" r="2" fill="#9f9a35"/><circle cx="18" cy="19" r="2" fill="#9f9a35"/></svg></span></div></article>
  <article class="card"><div class="photo p-wooden" role="img" aria-label="Studio headphones with wooden cups"></div><p class="card-name">Fontry Double Bed, Oak</p><p class="card-price">$749</p><div class="card-foot">Typical high street <s>$1,095*</s><span class="cart-btn"><svg width="16" height="15" viewBox="0 0 24 22"><path d="M1 2h4l3 12h12l3-9H7" fill="none" stroke="#9f9a35" stroke-width="2.4"/><circle cx="10" cy="19" r="2" fill="#9f9a35"/><circle cx="18" cy="19" r="2" fill="#9f9a35"/></svg></span></div></article>
  <article class="card"><div class="photo p-dark" role="img" aria-label="Black game controller"></div><p class="card-name">Fontry Double Bed, Oak</p><p class="card-price">$749</p><div class="card-foot">Typical high street <s>$1,095*</s><span class="cart-btn"><svg width="16" height="15" viewBox="0 0 24 22"><path d="M1 2h4l3 12h12l3-9H7" fill="none" stroke="#9f9a35" stroke-width="2.4"/><circle cx="10" cy="19" r="2" fill="#9f9a35"/><circle cx="18" cy="19" r="2" fill="#9f9a35"/></svg></span></div></article>
  <article class="card"><div class="photo p-dark" role="img" aria-label="Game console with controller and sensor"></div><p class="card-name">Fontry Double Bed, Oak</p><p class="card-price">$749</p><div class="card-foot">Typical high street <s>$1,095*</s><span class="cart-btn"><svg width="16" height="15" viewBox="0 0 24 22"><path d="M1 2h4l3 12h12l3-9H7" fill="none" stroke="#9f9a35" stroke-width="2.4"/><circle cx="10" cy="19" r="2" fill="#9f9a35"/><circle cx="18" cy="19" r="2" fill="#9f9a35"/></svg></span></div></article>
  <article class="card"><div class="photo p-tv" role="img" aria-label="Flat screen television with a bright orange picture"></div><p class="card-name">Fontry Double Bed, Oak</p><p class="card-price">$749</p><div class="card-foot">Typical high street <s>$1,095*</s><span class="cart-btn"><svg width="16" height="15" viewBox="0 0 24 22"><path d="M1 2h4l3 12h12l3-9H7" fill="none" stroke="#9f9a35" stroke-width="2.4"/><circle cx="10" cy="19" r="2" fill="#9f9a35"/><circle cx="18" cy="19" r="2" fill="#9f9a35"/></svg></span></div></article>
  <article class="card"><div class="photo p-silver" role="img" aria-label="Compact silver desktop computer"></div><p class="card-name">Fontry Double Bed, Oak</p><p class="card-price">$749</p><div class="card-foot">Typical high street <s>$1,095*</s><span class="cart-btn"><svg width="16" height="15" viewBox="0 0 24 22"><path d="M1 2h4l3 12h12l3-9H7" fill="none" stroke="#9f9a35" stroke-width="2.4"/><circle cx="10" cy="19" r="2" fill="#9f9a35"/><circle cx="18" cy="19" r="2" fill="#9f9a35"/></svg></span></div></article>
</main>

<nav class="pager">
  <span class="arrow">←</span>
  <span class="on">1</span><span class="bar">|</span><span>2</span><span class="bar">|</span><span>3</span><span class="bar">|</span><span>4</span><span class="bar">|</span><span>5</span>
  <span style="margin:0 8px">....</span><span>100</span>
  <span class="arrow">→</span>
</nav>
<p class="showing">Displaying 1 to 12 (of 100 products)</p>

<footer class="footer">
  <div class="footer-col" style="left:183px"><h4>Contact Us</h4>
    <ul>
      <li><svg width="9" height="12" viewBox="0 0 12 16"><path fill="#fff" d="M6 0a6 6 0 0 0-6 6c0 4.5 6 10 6 10s6-5.5 6-10a6 6 0 0 0-6-6zm0 8.5A2.5 2.5 0 1 1 6 3.5a2.5 2.5 0 0 1 0 5z"/></svg>17 Wrenfield, 42 Marlow</li>
      <li><svg width="11" height="11" viewBox="0 0 24 24"><path fill="#fff" d="M6.6 10.8a15 15 0 0 0 6.6 6.6l2.2-2.2c.3-.3.7-.4 1-.2 1.1.4 2.3.6 3.6.6.6 0 1 .4 1 1V20c0 .6-.4 1-1 1A17 17 0 0 1 3 4c0-.6.4-1 1-1h3.5c.6 0 1 .4 1 1 0 1.3.2 2.5.6 3.6.1.3 0 .7-.2 1z"/></svg>+000 (000) 0000</li>
      <li><svg width="11" height="9" viewBox="0 0 22 16"><rect width="22" height="16" fill="#fff"/><path d="M1 1l10 8 10-8" fill="none" stroke="#8f8b31" stroke-width="2"/></svg>mail@example.com</li>
    </ul></div>
  <div class="footer-col" style="left:398px"><h4>Information</h4>
    <ul><li>About Us</li><li>Privacy Policy</li><li>Terms &amp; Conditions</li><li>Secure Payment</li></ul></div>
  <div class="footer-col" style="left:612px"><h4>Costumer Service</h4>
    <ul><li>Contact Us</li><li>Return</li><li>FAQ</li><li>Site Map</li></ul></div>
  <div class="footer-col" style="left:828px"><h4>My Account</h4>
    <ul><li>My Account</li><li>Order History</li><li>Wish List</li><li>Newsletter</li></ul></div>
</footer>

<div class="bottombar">
  <p class="copyright">© 2014 Lumavorp. All rights reserved.</p>
  <div class="social"><span>plaztrove</span><span>chirpnest</span><span>gleamcircle</span></div>
</div>

</body>
</html>
```